Talon Microsystems PowerPoint Master Slide Deck Design

This is a 2-phase project to design a slide deck for a semiconductor company in the Silicon Valley. The design budget will be increased with each phase.
The slide deck will need to have one version with a dark background for presentations and a second version with a white background. Otherwise, the slides will be the same. I anticipate we will need a total of 10 slides, but that number may change.
The first phase will be to design a Title and a Title and Content slide.
- The Title Slide is the first slide of the deck. It should include the presentation title, the presenter's name and date of presentation
- The Title and Content slide should include a title and content with bullet points and up to 2 additional sub-bullets
- The Title and Content slide should have a footer that includes the slide #, Talon Microsystems Confidential, and the logo. This footer will be on every slide except the Title Slide
The first two slides will serve as the format for the remaining ~8 slides:
-Header and Content Text (1, 2, 4 column)
-Header and Content Image (bar chart, pie chart, tables)
-Break
-Title only
-Closing (Talon logo only)
Our slides contain a lot of content so a clean and simple design is best.
Both phases will need to include pre-set color options for
-Text and Lines
-Shadows
-Bullets and sub-bullets (including shapes, ex. circle, slash, square, etc.)
-Bar charts, pie charts, tables
Samples of our collateral are attached. Logo files are also attached
Look and feel
Each slider illustrates characteristics of the customer's brand and the style your logo design should communicate.

```html
<!DOCTYPE html>
<html lang="en">
<head>
<meta charset="utf-8">
<title>Talon Microsystems Slide Deck</title>
<link href="https://fonts.googleapis.com/css2?family=Poppins:wght@400;500;600&display=swap" rel="stylesheet">
<style>
:root{
  --brand:#0857ad;
  --brand-deep:#0a4f9e;
  --brand-light:#0a7bc4;
  --heading:#0b56a6;
  --ink:#4a4f57;
  --ink-dark:#2f3339;
  --grid:#9aa0a8;
  --page:#ffffff;
}
*{box-sizing:border-box;margin:0;padding:0}
html,body{width:1200px;height:4057px;overflow:hidden;background:var(--page)}
body{position:relative;font-family:"Poppins",sans-serif;color:var(--ink)}
.slide{position:absolute;left:52px;width:1100px;height:620px;background:var(--page);box-shadow:0 1px 5px rgba(0,0,0,.18);overflow:hidden}
.slide-title{top:52px;background:radial-gradient(ellipse at 68% 45%,#1fb6f0 0%,#0b5fc0 28%,#0a2f7a 60%,#071b4a 100%)}
.slide-about{top:723px}
.slide-services{top:1393px}
.slide-graph{top:2064px}
.slide-special{top:2735px}
.slide-closing{top:3404px;background:linear-gradient(135deg,#dfe8ef 0%,#e9eef2 45%,#e6ddd6 100%)}
.abs{position:absolute}
.title-text{color:#fff;left:27px;font-weight:500}
.title-main{top:448px;font-size:30px}
.title-sub{top:506px;font-size:23px}
.title-date{top:558px;font-size:23px}
.heading{position:absolute;color:var(--heading);font-size:21px;font-weight:500;letter-spacing:.2px}
.body-copy{position:absolute;font-size:10.3px;line-height:25.5px;color:var(--ink)}
.about-box{position:absolute;left:22px;top:146px;width:356px;height:368px;background:var(--brand);padding:24px 24px}
.about-box .body-copy{position:static;color:#fff}
.footer{position:absolute;left:0;top:553px;width:1100px;height:51px}
.footer-cap{position:absolute;left:0;top:0;width:47px;height:51px;background:var(--brand)}
.footer-brand{position:absolute;left:47px;top:0;width:163px;height:51px;display:flex;align-items:center;justify-content:center;gap:8px}
.brand-dot{width:14px;height:14px;border-radius:50%;background:var(--brand)}
.brand-name{font-size:24px;font-weight:500;color:var(--ink-dark);letter-spacing:.5px}
.footer-band{position:absolute;left:210px;top:0;width:890px;height:51px;background:var(--brand);color:#fff;font-size:15px;font-weight:500}
.footer-band .conf{position:absolute;left:210px;top:15px}
.footer-band .page{position:absolute;left:746px;top:15px;word-spacing:14px}
.photo{position:absolute;left:32px;top:51px;width:453px;height:453px;border-radius:16px;background:radial-gradient(circle at 45% 55%,#7fd3ff 0%,#1f86d8 30%,#0a3f8e 70%,#06214f 100%)}
.service{position:absolute;top:362px;width:100px;text-align:center}
.service-icon{display:block;margin:0 auto;width:63px;height:63px;border-radius:4px}
.service-label{display:block;margin-top:18px;font-size:14px;color:var(--brand)}
.chart{position:absolute;left:0;top:0}
.axis-label{font-size:14px;fill:#111;font-family:"Poppins",sans-serif}
.note{position:absolute;left:717px;width:345px;height:174px;background:#fff;box-shadow:0 0 5px rgba(0,0,0,.15);padding:24px 22px 0 44px}
.note .body-copy{position:static}
.note-mark{position:absolute;left:705px;width:31px;height:31px}
.spec-col{position:absolute;top:112px;width:415px}
.spec-lead{position:relative;padding-left:25px;font-size:11px;line-height:26px;color:var(--brand);font-weight:500}
.spec-lead::before{content:"";position:absolute;left:0;top:8px;width:10px;height:10px;border:1.5px solid var(--brand);border-radius:50%;background:radial-gradient(circle,var(--brand) 35%,transparent 40%)}
.spec-item{position:relative;margin-top:12px;padding-left:42px;font-size:10.3px;line-height:25.5px;color:var(--ink)}
.spec-item::before{content:"»";position:absolute;left:25px;top:0;font-weight:600;color:var(--ink-dark)}
.spec-item+.spec-item{margin-top:11px}
.closing-brand{position:absolute;left:0;top:0;width:1100px;height:620px;display:flex;align-items:center;justify-content:center;gap:26px}
.closing-brand .brand-dot{width:56px;height:56px}
.closing-brand .brand-name{font-size:70px;color:var(--ink-dark)}
</style>
</head>
<body>

<section class="slide slide-title" role="img" aria-label="Glowing blue microchip on a circuit board">
  <p class="abs title-text title-main">TALON MICROSYSTEMS</p>
  <p class="abs title-text title-sub">LOREM IPSUM</p>
  <p class="abs title-text title-date">13-12-2023</p>
</section>

<section class="slide slide-about">
  <h2 class="heading" style="left:58px;top:58px">ABOUT TALON MICROSYSTEMS</h2>
  <div class="about-box">
    <p class="body-copy">Sed ut perspiciatis unde omnis iste natus error sit voluptatem accusantium doloremque laudantium, totam rem aperiam, eaque ipsa quae ab illo inventore veritatis et quasi architecto beatae vitae dicta sunt explicabo. Nemo enim ipsam voluptatem quia voluptas sit aspernatur aut odit aut fugit, sed quia consequuntur magni dolores eos qui ratione voluptatem sequi nesciunt. Neque porro quisquam est, qui dolorem Excepteur sint occaecat cupidatat non proident, sunt in culpa qui officia deserunt mollit anim id est laborum. sed quia non numquam eius modi tempora incidunt ut labore et dolore magnam aliquam quaerat voluptatem.</p>
  </div>
  <p class="body-copy" style="left:420px;top:170px;width:302px">Sed ut perspiciatis unde omnis iste natus error sit voluptatem accusantium doloremque laudantium, totam rem aperiam, eaque ipsa quae ab illo inventore veritatis et quasi architecto beatae vitae dicta sunt explicabo. Nemo enim ipsam voluptatem quia voluptas sit aspernatur aut odit aut fugit, sed quia consequuntur magni dolores eos qui ratione voluptatem sequi nesciunt. Neque porro quisquam est, qui dolorem Excepteur sint occaecat cupidatat non proident, sunt in culpa qui officia deserunt mollit anim id est laborum. sed quia non numquam eius modi tempora incidunt ut labore et dolore magnam aliquam quaerat voluptatem.</p>
  <p class="body-copy" style="left:759px;top:170px;width:305px">Sed ut perspiciatis unde omnis iste natus error sit voluptatem accusantium doloremque laudantium, totam rem aperiam, eaque ipsa quae ab illo inventore veritatis et quasi architecto beatae vitae dicta sunt explicabo. Nemo enim ipsam voluptatem quia voluptas sit aspernatur aut odit aut fugit, sed quia consequuntur magni dolores eos qui ratione voluptatem sequi nesciunt. Neque porro quisquam est, qui dolorem Excepteur sint occaecat cupidatat non proident, sunt in culpa qui officia deserunt mollit anim id est laborum. sed quia non numquam eius modi tempora incidunt ut labore et dolore magnam aliquam quaerat voluptatem.</p>
  <footer class="footer"><div class="footer-cap"></div><div class="footer-brand"><span class="brand-dot"></span><span class="brand-name">TALON</span></div><div class="footer-band"><span class="conf">TALON MICROSYSTEMS CONFIDENTIAL</span><span class="page">PAGE | 02</span></div></footer>
</section>

<section class="slide slide-services">
  <div class="photo" role="img" aria-label="Blue processor chip on a printed circuit board"></div>
  <h2 class="heading" style="left:536px;top:66px">OUR SERVICES</h2>
  <p class="body-copy" style="left:536px;top:113px;width:505px">Lorem ipsum dolor sit amet, consectetur adipiscing elit, sed do eiusmod tempor incididunt ut labore et dolore magna aliqua. Ut enim ad minim veniam, quis nostrud exercitation ullamco laboris nisi ut aliquip ex ea commodo consequat. Duis aute irure dolor in reprehenderit in voluptate velit esse cillum dolore eu fugiat nulla pariatur. Excepteur sint occaecat cupidatat non proident, sunt in culpa qui officia deserunt mollit anim id est laborum. Sed ut perspiciatis unde omnis iste natus error sit voluptatem accusantium doloremque laudantium, totam rem aperiam, eaque ipsa quae ab illo inventore veritatis et quasi architecto beatae vitae dicta sunt explicabo. Nemo enim ipsam voluptatem quia voluptas sit aspernatur aut odit aut fugit</p>
  <div class="service" style="left:522px"><svg class="service-icon" viewBox="0 0 63 63" aria-hidden="true"><rect width="63" height="63" rx="4" fill="#0857ad"/><rect x="19" y="19" width="25" height="25" fill="none" stroke="#fff" stroke-width="2"/><path d="M24 13v6M31 13v6M38 13v6M24 44v6M31 44v6M38 44v6M13 24h6M13 31h6M13 38h6M44 24h6M44 31h6M44 38h6" stroke="#fff" stroke-width="2"/></svg><span class="service-label">LOREM IPSUM</span></div>
  <div class="service" style="left:666px"><svg class="service-icon" viewBox="0 0 63 63" aria-hidden="true"><rect width="63" height="63" rx="4" fill="#0857ad"/><rect x="17" y="17" width="29" height="29" rx="3" fill="none" stroke="#fff" stroke-width="2"/><rect x="25" y="25" width="13" height="13" fill="none" stroke="#fff" stroke-width="2"/><path d="M23 11v6M31 11v6M39 11v6M23 46v6M31 46v6M39 46v6" stroke="#fff" stroke-width="2"/></svg><span class="service-label">LOREM IPSUM</span></div>
  <div class="service" style="left:810px"><svg class="service-icon" viewBox="0 0 63 63" aria-hidden="true"><rect width="63" height="63" rx="4" fill="#0857ad"/><rect x="22" y="22" width="19" height="19" fill="none" stroke="#fff" stroke-width="2"/><path d="M31 22V11M31 41v11M22 31H11M41 31h11M24 22l-7-7M39 22l7-7M24 41l-7 7M39 41l7 7" stroke="#fff" stroke-width="2"/></svg><span class="service-label">LOREM IPSUM</span></div>
  <div class="service" style="left:954px"><svg class="service-icon" viewBox="0 0 63 63" aria-hidden="true"><rect width="63" height="63" rx="4" fill="#0857ad"/><circle cx="31.5" cy="31.5" r="14" fill="none" stroke="#fff" stroke-width="2"/><circle cx="31.5" cy="31.5" r="6" fill="none" stroke="#fff" stroke-width="2"/><path d="M31.5 11v6M31.5 46v6M11 31.5h6M46 31.5h6M17 17l4 4M42 42l4 4M46 17l-4 4M21 42l-4 4" stroke="#fff" stroke-width="2"/></svg><span class="service-label">LOREM IPSUM</span></div>
  <footer class="footer"><div class="footer-cap"></div><div class="footer-brand"><span class="brand-dot"></span><span class="brand-name">TALON</span></div><div class="footer-band"><span class="conf">TALON MICROSYSTEMS CONFIDENTIAL</span><span class="page">PAGE | 03</span></div></footer>
</section>

<section class="slide slide-graph">
  <h2 class="heading" style="left:49px;top:52px">OUR GRAPH</h2>
  <svg class="chart" width="680" height="540" viewBox="0 0 680 540" role="img" aria-label="Bar chart with two series across four categories">
    <g stroke="#9aa0a8" stroke-width="1">
      <line x1="87" y1="166" x2="640" y2="166"/><line x1="87" y1="218" x2="640" y2="218"/><line x1="87" y1="271" x2="640" y2="271"/><line x1="87" y1="323" x2="640" y2="323"/><line x1="87" y1="375" x2="640" y2="375"/><line x1="87" y1="428" x2="640" y2="428"/><line x1="87" y1="480" x2="640" y2="480"/>
    </g>
    <g class="axis-label" text-anchor="end">
      <text x="72" y="171">6</text><text x="72" y="223">5</text><text x="72" y="276">4</text><text x="72" y="328">3</text><text x="72" y="380">2</text><text x="72" y="433">1</text><text x="72" y="485">0</text>
    </g>
    <g fill="#0a4f9e">
      <rect x="135" y="323" width="12" height="157"/><rect x="264" y="260" width="12" height="220"/><rect x="397" y="370" width="12" height="110"/><rect x="539" y="239" width="12" height="241"/>
    </g>
    <g fill="#0a7bc4">
      <rect x="160" y="292" width="12" height="188"/><rect x="288" y="224" width="12" height="256"/><rect x="421" y="349" width="12" height="131"/><rect x="564" y="197" width="12" height="283"/>
    </g>
    <g class="axis-label" text-anchor="middle">
      <text x="153" y="517">CATEGORY 1</text><text x="282" y="517">CATEGORY 2</text><text x="415" y="517">CATEGORY 3</text><text x="557" y="517">CATEGORY 4</text>
    </g>
  </svg>
  <div class="note" style="top:84px"><p class="body-copy">Lorem ipsum dolor sit amet, consectetur adipiscing elit, sed do eiusmod tempor incididunt ut labore et dolore magna aliqua. Ut enim ad minim veniam, quis nostrud exercitation ullamco laboris nisi ut aliquip ex ea commodo consequat. Duis aute irure</p></div>
  <div class="note-mark" style="top:155px;background:var(--brand-deep)"></div>
  <div class="note" style="top:295px"><p class="body-copy">Lorem ipsum dolor sit amet, consectetur adipiscing elit, sed do eiusmod tempor incididunt ut labore et dolore magna aliqua. Ut enim ad minim veniam, quis nostrud exercitation ullamco laboris nisi ut aliquip ex ea commodo consequat. Duis aute irure</p></div>
  <div class="note-mark" style="top:366px;background:var(--brand-light)"></div>
  <footer class="footer"><div class="footer-cap"></div><div class="footer-brand"><span class="brand-dot"></span><span class="brand-name">TALON</span></div><div class="footer-band"><span class="conf">TALON MICROSYSTEMS CONFIDENTIAL</span><span class="page">PAGE | 04</span></div></footer>
</section>

<section class="slide slide-special">
  <h2 class="heading" style="left:82px;top:50px">OUR SPECIALIZATION</h2>
  <div class="spec-col" style="left:88px">
    <p class="spec-lead">Lorem ipsum dolor sit amet, consectetur adipiscing elit, sed do eiusmod tempor incididunt ut labore et dolore magna aliqua.</p>
    <p class="spec-item">Sed ut perspiciatis unde omnis iste natus error sit voluptatem accusantium doloremque laudantium, totam rem aperiam, eaque ipsa quae ab illo inventore veritatis et quasi architecto beatae vitae dicta sunt explicabo.</p>
    <p class="spec-item">Sed ut perspiciatis unde omnis iste natus error sit voluptatem accusantium doloremque laudantium, totam rem aperiam, eaque ipsa quae ab illo inventore veritatis et quasi architecto beatae vitae dicta sunt explicabo.</p>
    <p class="spec-item">Sed ut perspiciatis unde omnis iste natus error sit voluptatem accusantium doloremque laudantium, totam rem aperiam, eaque ipsa quae ab illo inventore veritatis et quasi architecto beatae vitae dicta sunt explicabo.</p>
  </div>
  <div class="spec-col" style="left:585px">
    <p class="spec-lead">Lorem ipsum dolor sit amet, consectetur adipiscing elit, sed do eiusmod tempor incididunt ut labore et dolore magna aliqua.</p>
    <p class="spec-item">Sed ut perspiciatis unde omnis iste natus error sit voluptatem accusantium doloremque laudantium, totam rem aperiam, eaque ipsa quae ab illo inventore veritatis et quasi architecto beatae vitae dicta sunt explicabo.</p>
    <p class="spec-item">Sed ut perspiciatis unde omnis iste natus error sit voluptatem accusantium doloremque laudantium, totam rem aperiam, eaque ipsa quae ab illo inventore veritatis et quasi architecto beatae vitae dicta sunt explicabo.</p>
    <p class="spec-item">Sed ut perspiciatis unde omnis iste natus error sit voluptatem accusantium doloremque laudantium, totam rem aperiam, eaque ipsa quae ab illo inventore veritatis et quasi architecto beatae vitae dicta sunt explicabo.</p>
  </div>
  <footer class="footer"><div class="footer-cap"></div><div class="footer-brand"><span class="brand-dot"></span><span class="brand-name">TALON</span></div><div class="footer-band"><span class="conf">TALON MICROSYSTEMS CONFIDENTIAL</span><span class="page">PAGE | 05</span></div></footer>
</section>

<section class="slide slide-closing" role="img" aria-label="Faded circuit board background with the Talon Microsystems name">
  <div class="closing-brand"><span class="brand-dot"></span><span class="brand-name">Talon Microsystems</span></div>
</section>

</body>
</html>
```